BUSINESS CARD DESIGN

NAME- DALE VORSKIN
PHONE NUMER - 555- 714-9082
EMAIL- OFFICE@TRV-GROUNDMAKRZ.COM
BACK OF CARD- SPEACIALIZES IN LAND CLEARING, FORESTRY MUCLHING AND EXCAVATION

Contact Information for Business Card

NAME- DALE VORSKIN PHONE NUMER - 555- 714-9082 EMAIL- OFFICE@TRV-GROUNDMAKRZ.COM BACK OF CARD- SPEACIALIZES IN LAND CLEARING , MUCLHING AND EXCAVATION

```html
<!DOCTYPE html>
<html lang="en">
<head>
<meta charset="utf-8">
<title>Terravale Groundmakrz – Business Card</title>
<link href="https://fonts.googleapis.com/css2?family=Audiowide&family=Roboto:wght@400;500&display=swap" rel="stylesheet">
<style>
  :root {
    --stage: #18181a;
    --card: #2a2a2c;
    --card-edge: #333336;
    --gold: #f9c515;
    --amber: #f7941d;
    --ink: #ffffff;
    --dark-ink: #2a2a2c;
  }
  * { margin: 0; padding: 0; box-sizing: border-box; }
  html, body { width: 1200px; height: 840px; overflow: hidden; background: var(--stage); }
  .stage {
    width: 1200px; height: 840px;
    display: flex; flex-direction: column; align-items: center; justify-content: center; gap: 52px;
  }
  .card {
    position: relative; width: 620px; height: 354px;
    background: linear-gradient(135deg, var(--card-edge), var(--card));
    border-radius: 22px; overflow: hidden;
  }
  /* Back */
  .card--back { border-bottom: 5px solid var(--gold); }
  .brand {
    font-family: "Audiowide", sans-serif; color: var(--gold);
    text-transform: uppercase; line-height: 1.1;
  }
  .back-brand {
    position: absolute; top: 70px; left: 0; right: 0; text-align: center;
  }
  .back-brand .brand-name { font-size: 34px; letter-spacing: 1px; }
  .back-brand .brand-sub { font-size: 16px; letter-spacing: 9px; margin-top: 6px; }
  .rule { height: 3px; background: var(--gold); }
  .back-brand .rule { width: 300px; margin: 14px auto 0; }
  .specialty-band {
    position: absolute; top: 200px; left: 50%; transform: translateX(-50%);
    background: var(--gold); color: var(--dark-ink);
    font-family: "Audiowide", sans-serif; font-size: 22px; padding: 6px 18px;
    text-transform: uppercase; white-space: nowrap;
  }
  .services {
    position: absolute; top: 262px; left: 0; right: 0; text-align: center;
    font-family: "Roboto", sans-serif; font-size: 19px; color: var(--ink);
    text-transform: uppercase; letter-spacing: .3px;
  }
  .services .dot { color: var(--gold); margin: 0 8px; }
  /* Front */
  .front-brand { position: absolute; top: 42px; left: 42px; }
  .front-brand .brand-name { font-size: 27px; }
  .front-brand .brand-sub { font-size: 13px; letter-spacing: 7px; margin-top: 4px; padding-left: 40px; }
  .front-brand .rule { width: 250px; margin-top: 10px; }
  .wave { position: absolute; inset: 0; }
  .holder {
    position: absolute; top: 186px; left: 70px;
    font-family: "Audiowide", sans-serif; font-size: 30px; color: var(--gold);
  }
  .contact {
    position: absolute; top: 240px; left: 70px; list-style: none;
    font-family: "Roboto", sans-serif; font-size: 20px; color: var(--ink);
  }
  .contact li { display: flex; align-items: center; gap: 10px; margin-bottom: 8px; }
  .contact svg { width: 20px; height: 20px; fill: var(--amber); flex: none; }
</style>
</head>
<body>
<main class="stage">
  <section class="card card--back">
    <div class="back-brand brand">
      <div class="brand-name">Terravale Groundmakrz</div>
      <div class="brand-sub">LLC</div>
      <div class="rule"></div>
    </div>
    <div class="specialty-band">Speacializes in</div>
    <p class="services"><span class="dot">●</span>Land clearing<span class="dot">●</span>Muclhing<span class="dot">●</span>Excavation</p>
  </section>

  <section class="card card--front">
    <svg class="wave" viewBox="0 0 620 354" preserveAspectRatio="none" aria-hidden="true">
      <defs>
        <linearGradient id="waveFill" x1="0" y1="1" x2="1" y2="0">
          <stop offset="0" stop-color="#f7941d"/>
          <stop offset=".35" stop-color="#f9c515"/>
          <stop offset="1" stop-color="#f9c515"/>
        </linearGradient>
      </defs>
      <path d="M150 354 C 250 330, 300 260, 360 230 C 440 190, 540 210, 620 150 L 620 354 Z" fill="url(#waveFill)"/>
    </svg>
    <div class="front-brand brand">
      <div class="brand-name">Terravale Groundmakrz</div>
      <div class="brand-sub">LLC</div>
      <div class="rule"></div>
    </div>
    <div class="holder">DALE VORSKIN</div>
    <ul class="contact">
      <li>
        <svg viewBox="0 0 24 24"><path d="M6.6 10.8a15.1 15.1 0 0 0 6.6 6.6l2.2-2.2c.3-.3.7-.4 1-.2 1.1.4 2.3.6 3.6.6.6 0 1 .4 1 1V20c0 .6-.4 1-1 1A17 17 0 0 1 3 4c0-.6.4-1 1-1h3.5c.6 0 1 .4 1 1 0 1.3.2 2.5.6 3.6.1.3 0 .7-.2 1z"/></svg>
        555- 714-9082
      </li>
      <li>
        <svg viewBox="0 0 24 24"><path d="M3 5h18v14H3z M4.5 6.5 12 12l7.5-5.5" fill="none" stroke="#f7941d" stroke-width="2"/></svg>
        office@trv-groundmakrz.com
      </li>
    </ul>
  </section>
</main>
</body>
</html>
```